Korvile

I'd like new business card design options. I'll need to provide updated contact info although after the deign is complete. We are in IT, specifically in the data backup, archiving and disaster recovery verticals.

Industry/Entity Type

Business

```html
<!DOCTYPE html>
<html lang="en">
<head>
<meta charset="utf-8">
<title>Korvile – Business Card</title>
<link rel="stylesheet" href="https://fonts.googleapis.com/css2?family=Arimo:wght@400;700&display=swap">
<style>
  :root {
    --backdrop: #1c1d20;
    --card-white: #ffffff;
    --brand-blue: #1656b0;
    --brand-blue-deep: #0f4a9e;
    --brand-blue-light: #2a78d0;
    --accent-sky: #3f8fe0;
    --ink: #2a2a2a;
    --on-blue: #eef4fc;
  }
  * { box-sizing: border-box; margin: 0; padding: 0; }
  html, body { width: 1200px; height: 963px; overflow: hidden; }
  body {
    background: var(--backdrop);
    font-family: "Arimo", Arial, sans-serif;
    position: relative;
  }
  .card {
    position: absolute;
    top: 331px;
    width: 525px;
    height: 300px;
    border-radius: 14px;
    overflow: hidden;
  }
  /* Front */
  .card-front { left: 60px; background: var(--card-white); }
  .front-wave { position: absolute; inset: 0; }
  .brand-block { position: absolute; left: 26px; top: 84px; }
  .brand-row { display: flex; align-items: center; gap: 10px; }
  .brand-dot {
    width: 34px; height: 34px; border-radius: 50%;
    background: var(--accent-sky);
  }
  .brand-name {
    font-weight: 700; font-size: 28px; letter-spacing: 3px;
    color: var(--brand-blue);
  }
  .divider {
    position: absolute; left: 250px; top: 52px;
    width: 1.5px; height: 150px; background: var(--brand-blue);
  }
  .contact { position: absolute; left: 264px; right: 14px; top: 52px; color: var(--ink); }
  .contact-name { font-size: 17px; font-weight: 700; color: var(--brand-blue); white-space: nowrap; }
  .contact-title { font-size: 13px; margin-top: 2px; }
  .contact-address { font-size: 12.5px; line-height: 1.3; margin-top: 6px; }
  .contact-lines { list-style: none; margin-top: 6px; font-size: 12.5px; line-height: 1.35; }
  .contact-lines li { display: flex; align-items: center; gap: 6px; }
  .contact-lines svg { width: 10px; height: 10px; fill: var(--brand-blue); flex: none; }

  /* Back */
  .card-back {
    left: 615px;
    background: linear-gradient(160deg, var(--brand-blue-light) 0%, var(--brand-blue) 45%, var(--brand-blue-deep) 100%);
    color: var(--on-blue);
  }
  .back-brand { position: absolute; left: 0; right: 0; top: 100px; display: flex; justify-content: center; }
  .back-brand .brand-row { gap: 14px; }
  .back-brand .brand-dot { width: 58px; height: 58px; background: #9fc8ef; }
  .back-brand .brand-name { color: var(--on-blue); font-size: 44px; letter-spacing: 6px; }
  .service-line {
    position: absolute; left: 0; right: 0; bottom: 34px; text-align: center;
    font-size: 11.5px; letter-spacing: 0.5px; color: var(--on-blue);
  }
</style>
</head>
<body>
  <section class="card card-front">
    <svg class="front-wave" viewBox="0 0 525 300" aria-hidden="true">
      <path d="M0,196 C140,250 300,215 412,300 L0,300 Z" fill="var(--accent-sky)"/>
      <path d="M0,208 C140,262 292,228 398,300 L0,300 Z" fill="var(--card-white)"/>
      <path d="M0,214 C140,268 288,236 388,300 L0,300 Z" fill="var(--brand-blue)"/>
    </svg>
    <div class="brand-block">
      <div class="brand-row">
        <span class="brand-dot"></span>
        <span class="brand-name">KORVILE</span>
      </div>
    </div>
    <div class="divider"></div>
    <div class="contact">
      <div class="contact-name">Daniel R. Whitcombe, Ph.D.</div>
      <div class="contact-title">President, CTO</div>
      <div class="contact-address">240 North Alder Street<br>Brenford, Ohio 43210</div>
      <ul class="contact-lines">
        <li><svg viewBox="0 0 10 10"><path d="M2,0 L4,2 L3,3.5 Q4.5,6 6.5,7 L8,6 L10,8 L8.5,10 Q3,9.5 0,2 Z"/></svg>800.555.0142</li>
        <li><svg viewBox="0 0 10 10"><rect x="0" y="3" width="10" height="5" rx="1"/><rect x="2" y="0" width="6" height="3"/></svg>928.555.0187</li>
        <li><svg viewBox="0 0 10 10"><circle cx="5" cy="5" r="4.3" fill="none" stroke="var(--brand-blue)" stroke-width="1.2"/><path d="M0.7,5 H9.3 M5,0.7 V9.3" stroke="var(--brand-blue)" stroke-width="1"/></svg>www.korvile.com</li>
        <li><svg viewBox="0 0 10 10"><rect x="0.5" y="2" width="9" height="6.5" fill="none" stroke="var(--brand-blue)" stroke-width="1.2"/><path d="M0.5,2 L5,6 L9.5,2" fill="none" stroke="var(--brand-blue)" stroke-width="1.1"/></svg>daniel.whitcombe@korvile.com</li>
      </ul>
    </div>
  </section>

  <section class="card card-back">
    <div class="back-brand">
      <div class="brand-row">
        <span class="brand-dot"></span>
        <span class="brand-name">KORVILE</span>
      </div>
    </div>
    <div class="service-line">ONLINE PC BACKUP - CONINUOUS SERVER BACKUP - DATA ARCHIVING</div>
  </section>
</body>
</html>
```